Korvalith Brochure Design - IT Services - Modern Design - Services List

Hi,

We are looking for a modern IT Services brochure design of between 4 - 6 pages, it must be based on a blue and white colour theme with some nice technical imagery. It would need a section about why Korvalith and a contact section at the end.

Here is some info that could be included

Target Market(s)

Medium to Large Businesses

Industry/Entity Type

Information Technology

Colors
0054AA
0677BA
7BADD7
CADEEF
E8F1F8

Requirements
Must have
• Striking technical imagery
Nice to have
• Nice Icons to list the different services sections

```html
<!DOCTYPE html>
<html lang="en">
<head>
<meta charset="utf-8">
<title>Korvalith IT Services Brochure</title>
<link rel="stylesheet" href="https://fonts.googleapis.com/css2?family=Raleway:wght@400;600;700&family=Roboto:wght@300;400;500;700&family=Roboto+Condensed:wght@300;400&display=swap">
<style>
:root{
  --bg:#a7a7a7;
  --navy:#0d0f1c;
  --blue:#1b8fce;
  --blue-deep:#0677ba;
  --blue-soft:#7badd7;
  --white:#ffffff;
  --ink:#1a1a1a;
  --grey-band:#4a4a4e;
}
*{box-sizing:border-box;margin:0;padding:0}
html,body{width:1200px;height:1200px;overflow:hidden}
body{background:var(--bg);position:relative;font-family:"Roboto",sans-serif;color:var(--ink)}
.sheet{position:absolute;overflow:hidden}
.sheet--outer{left:266px;top:19px;width:725px;height:563px}
.sheet--inner{left:266px;top:607px;width:739px;height:575px}
.panel{position:absolute;top:0;height:100%;overflow:hidden}
.panel--white{background:var(--white)}
.panel--navy{background:var(--navy);color:var(--white)}
.abs{position:absolute}
svg.art{position:absolute;left:0;top:0}

.body-copy{font-size:8.6px;line-height:1.28;text-align:justify;font-weight:300}
.panel--navy .body-copy{font-weight:400}
.why-copy{font-size:8.3px;line-height:10.7px;letter-spacing:-0.12px;text-align:justify;font-weight:400}
.why-block{position:absolute;left:16px;width:206px}
.dot-list{list-style:none}
.dot-list li{position:relative;padding-left:15px;font-size:8.4px;line-height:1.28;margin-bottom:7px;text-align:justify;font-family:"Roboto Condensed",sans-serif;font-weight:400}
.panel--navy .dot-list li{font-family:"Roboto",sans-serif;font-weight:400}
.dot-list li::before{content:"";position:absolute;left:0;top:2px;width:6px;height:6px;border-radius:50%;background:var(--blue)}
.head{font-family:"Roboto",sans-serif;font-weight:500;font-size:16px;color:var(--white);padding-bottom:3px;position:relative;display:inline-block}
.head::after{content:"";position:absolute;left:0;bottom:-2px;height:1.5px;background:var(--blue);width:var(--rule,100%)}
.head--blue{font-family:"Raleway",sans-serif;font-weight:700;color:var(--blue);font-size:16px}
.sub{font-family:"Raleway",sans-serif;font-weight:700;color:var(--blue);font-size:10.3px;line-height:12px}
.num-list{list-style:none}
.num-list li{position:relative;padding-left:20px;font-size:8.6px;line-height:1.28;margin-bottom:7px;text-align:justify;font-weight:300;font-family:"Roboto Condensed",sans-serif}
.num-list li span{position:absolute;left:0;top:0;color:var(--blue);font-family:"Raleway",sans-serif;font-weight:700;font-size:9px}

.wordmark{text-align:right;line-height:1}
.wordmark__name{font-family:"Raleway",sans-serif;font-weight:700;color:var(--blue);letter-spacing:0.5px;display:block}
.wordmark__tag{font-family:"Roboto",sans-serif;font-weight:500;color:#333;display:block;margin-top:3px}

.contact{list-style:none}
.contact li{display:flex;align-items:center;gap:8px;font-size:9px;margin-bottom:13px;height:12px}
.contact svg{flex:none}
</style>
</head>
<body>

<section class="sheet sheet--outer">

  <div class="panel panel--white" style="left:0;width:243px">
    <ul class="dot-list abs" style="left:25px;top:23px;width:198px">
      <li>IT Strategy and Planning: Strategic guidance to align your IT initiatives with your business objectives.</li>
      <li>Technology Assessments: In-depth evaluations to optimize your IT infrastructure.</li>
      <li>Project Management: Expert management of IT projects from inception to completion.</li>
      <li>Business Continuity Planning: Strategies to ensure your business remains operational during disruptions.</li>
    </ul>
    <svg class="art" width="243" height="563" viewBox="0 0 243 563">
      <defs>
        <linearGradient id="officeTone" x1="0" y1="0" x2="1" y2="1">
          <stop offset="0" stop-color="#1e1a17"/>
          <stop offset="0.6" stop-color="#4a3c30"/>
          <stop offset="1" stop-color="#7a6a5a"/>
        </linearGradient>
      </defs>
      <path d="M0,228 Q200,262 243,563 L0,563 Z" fill="var(--navy)"/>
      <path d="M0,240 Q190,270 236,563 L0,563 Z" fill="var(--blue)"/>
      <path d="M0,255 Q180,285 226,563 L0,563 Z" fill="var(--white)"/>
      <path d="M0,263 Q172,292 220,563 L0,563 Z" fill="url(#officeTone)" role="img" aria-label="Photo: two colleagues reviewing work at a desktop computer in an office"/>
    </svg>
    <div class="wordmark abs" style="right:16px;top:263px">
      <span class="wordmark__name" style="font-size:18px">KORVALITH</span>
      <span class="wordmark__tag" style="font-size:4.5px">COMPUTING EXCELLENCE</span>
    </div>
  </div>

  <div class="panel panel--navy" style="left:243px;width:237px">
    <div class="abs" style="left:16px;top:19px">
      <h2 class="head" style="font-size:16px">Why Choose Korvalith?</h2>
    </div>
    <div class="why-block" style="top:52px">
      <h3 class="sub">Expertise and Experience</h3>
      <p class="why-copy">With years of experience in the IT industry, our team possesses the knowledge and skills to tackle any challenge. We stay abreast of the latest technological advancements to provide you with cutting-edge solutions.</p>
    </div>
    <div class="why-block" style="top:116px">
      <h3 class="sub">Customer-Centric Approach</h3>
      <p class="why-copy">We prioritize our clients' needs and work closely with them to deliver customized solutions that drive success. Our client-centric approach ensures that we are always aligned with your business goals</p>
    </div>
    <div class="why-block" style="top:183px">
      <h3 class="sub">Proactive Support</h3>
      <p class="why-copy">Our proactive support model ensures that potential issues are identified and resolved before they can impact your operations. We are committed to maintaining the highest levels of service availability and performance.</p>
    </div>
    <div class="why-block" style="top:248px">
      <h3 class="sub">Comprehensive Solutions</h3>
      <p class="why-copy">From managed services to cybersecurity, we offer a comprehensive suite of IT solutions designed to meet the diverse needs of your business. Our holistic approach ensures that all aspects of your IT infrastructure are covered</p>
    </div>
    <div class="abs" style="left:93px;top:318px;width:52px;height:52px;border-radius:50%;background:var(--white);border:1.5px solid var(--blue);display:flex;align-items:center;justify-content:center">
      <span style="font-family:'Raleway',sans-serif;font-weight:700;color:var(--blue);font-size:7px">KORVALITH</span>
    </div>
    <div class="abs" style="left:0;width:237px;top:391px;text-align:center">
      <span class="head" style="font-size:12px;--rule:60%;font-weight:400">COMPUTING EXCELLENCE</span>
    </div>
    <div class="abs" style="left:16px;top:427px">
      <h2 class="head" style="font-size:12.5px">Get in Touch&nbsp;&nbsp;&nbsp;&nbsp;&nbsp;&nbsp;&nbsp;&nbsp;</h2>
    </div>
    <ul class="contact abs" style="left:16px;top:456px">
      <li><svg width="13" height="13" viewBox="0 0 13 13"><circle cx="6.5" cy="6.5" r="6" fill="none" stroke="var(--blue)"/><circle cx="6.5" cy="6.5" r="4.6" fill="var(--blue)"/><path d="M4.6,4 l1,0 .5,1.3 -.6.5 a3,3 0 0 0 1.7,1.7 l.5-.6 1.3.5 0,1 a.6.6 0 0 1-.6.6 A4.4,4.4 0 0 1 4,4.6 a.6.6 0 0 1 .6-.6Z" fill="#fff"/></svg>+44 020 555 0148</li>
      <li><svg width="13" height="13" viewBox="0 0 13 13"><circle cx="6.5" cy="6.5" r="6" fill="none" stroke="var(--blue)"/><circle cx="6.5" cy="6.5" r="4.6" fill="var(--blue)"/><rect x="4" y="4.8" width="5" height="3.5" fill="#fff"/><path d="M4,4.8 l2.5,2 2.5-2" fill="none" stroke="var(--blue)" stroke-width=".6"/></svg>info@korvalith.co.uk</li>
      <li><svg width="13" height="13" viewBox="0 0 13 13"><circle cx="6.5" cy="6.5" r="6" fill="none" stroke="var(--blue)"/><circle cx="6.5" cy="6.5" r="4.6" fill="var(--blue)"/><path d="M4.8,8.2 l3.4-3.4" stroke="#fff" stroke-width=".9"/></svg>www.korvalith.co.uk</li>
      <li><svg width="13" height="13" viewBox="0 0 13 13"><circle cx="6.5" cy="6.5" r="6" fill="none" stroke="var(--blue)"/><circle cx="6.5" cy="6.5" r="4.6" fill="var(--blue)"/><path d="M6.5,9.5 C5,7.6 4.6,6.8 4.6,5.9 a1.9,1.9 0 0 1 3.8,0 c0,.9 -.4,1.7 -1.9,3.6Z" fill="#fff"/><circle cx="6.5" cy="5.9" r=".7" fill="var(--blue)"/></svg>48 Harbor Lane, Westbrook Park, London, UK</li>
    </ul>
  </div>

  <div class="panel panel--white" style="left:480px;width:245px">
    <svg class="art" width="245" height="563" viewBox="0 0 245 563">
      <defs>
        <linearGradient id="techTone" x1="0" y1="0" x2="1" y2="1">
          <stop offset="0" stop-color="#3f86a8"/>
          <stop offset="0.5" stop-color="#236a8c"/>
          <stop offset="1" stop-color="#0d1a26"/>
        </linearGradient>
      </defs>
      <path d="M0,0 L245,0 L245,330 Q170,260 112,236 Q50,268 0,300 Z" fill="var(--navy)"/>
      <path d="M0,0 L245,0 L245,318 Q170,250 112,226 Q50,258 0,290 Z" fill="var(--blue)"/>
      <path d="M0,0 L245,0 L245,302 Q170,236 112,212 Q50,244 0,278 Z" fill="var(--navy)"/>
      <path d="M0,0 L245,0 L245,292 Q170,228 112,204 Q50,236 0,270 Z" fill="url(#techTone)" role="img" aria-label="Photo: hand holding a tablet with glowing cloud network graphics"/>
    </svg>
    <div class="wordmark abs" style="left:15px;top:340px;width:183px">
      <span class="wordmark__name" style="font-size:30px;text-align:left">KORVALITH</span>
      <span class="wordmark__tag" style="font-size:7.5px">COMPUTING EXCELLENCE</span>
    </div>
    <div class="abs" style="left:15px;top:414px;width:225px;font-family:'Raleway',sans-serif">
      <div style="color:var(--blue);font-weight:700;font-size:22.5px;line-height:1.05">Empowering Your</div>
      <div style="color:#222;font-weight:400;font-size:16px;line-height:1.3">Business with Cutting-Edge</div>
      <div style="color:var(--blue);font-weight:700;font-size:16px;line-height:1.2">IT Solutions</div>
    </div>
    <div class="abs" style="left:15px;top:521px;display:flex;align-items:center;gap:10px">
      <svg width="16" height="16" viewBox="0 0 16 16" fill="none" stroke="var(--blue)" stroke-width="1.3"><rect x="1" y="7" width="8" height="4.5" rx="2.25" transform="rotate(-45 5 9.25)"/><rect x="7" y="4.5" width="8" height="4.5" rx="2.25" transform="rotate(-45 11 6.75)"/></svg>
      <span style="font-family:'Raleway',sans-serif;font-weight:700;font-size:11px;color:#111">www.korvalith.co.uk</span>
    </div>
  </div>
</section>

<section class="sheet sheet--inner">
  <div class="panel panel--navy" style="left:0;width:249px"></div>
  <div class="panel panel--white" style="left:249px;width:241px"></div>
  <div class="panel panel--navy" style="left:490px;width:249px"></div>

  <svg class="art" width="490" height="270" viewBox="0 0 490 270">
    <defs>
      <linearGradient id="teamTone" x1="0" y1="0" x2="1" y2="1">
        <stop offset="0" stop-color="#3c4a3a"/>
        <stop offset="0.5" stop-color="#4f6f95"/>
        <stop offset="1" stop-color="#8fa9c8"/>
      </linearGradient>
    </defs>
    <path d="M0,0 L473,0 Q340,230 0,250 Z" fill="var(--grey-band)"/>
    <path d="M0,0 L470,0 Q335,220 0,238 Z" fill="var(--blue)"/>
    <path d="M0,0 L466,0 Q330,212 0,228 Z" fill="url(#teamTone)" role="img" aria-label="Photo: team of five colleagues gathered around a laptop in a bright office"/>
    <path d="M0,228 Q330,212 466,0 L470,0 Q330,90 0,180 Z" fill="var(--blue)" opacity="0.25"/>
  </svg>

  <div class="abs" style="left:25px;top:296px;width:209px;color:var(--white)">
    <h2 class="head" style="--rule:62%">About Korvalith</h2>
    <p class="body-copy" style="margin-top:14px;font-weight:300;font-family:'Roboto Condensed',sans-serif;font-size:9px">At Korvalith, we are dedicated to providing top-tier IT services that drive efficiency, innovation, and growth for your business. With a commitment to excellence and a team of highly skilled professionals, we offer a comprehensive suite of solutions tailored to meet the unique needs of our clients.</p>
    <h2 class="head" style="--rule:58%;margin-top:14px">Our Services</h2>
    <h3 class="sub" style="margin-top:16px;font-size:11px">Managed IT Services</h3>
    <p class="body-copy" style="margin-top:12px;font-weight:300">Our Managed IT Services provide proactive monitoring and management of your IT infrastructure, ensuring maximum uptime and reliability.</p>
  </div>

  <div class="wordmark abs" style="left:350px;top:151px;width:123px">
    <span class="wordmark__name" style="font-size:18px">KORVALITH</span>
    <span class="wordmark__tag" style="font-size:4.5px">COMPUTING EXCELLENCE</span>
  </div>
  <div class="abs" style="left:265px;top:208px;width:210px">
    <h2 class="head head--blue">We offer:</h2>
    <ol class="num-list" style="margin-top:10px">
      <li><span>01.</span>24/7 Network Monitoring: Continuous monitoring to detect and resolve issues before they impact your business.</li>
      <li><span>02.</span>Helpdesk Support: Responsive and knowledgeable support team available round the clock.</li>
      <li><span>03.</span>Patch Management: Regular updates and patches to keep your systems secure and up-to-date.</li>
      <li><span>04.</span>IT Asset Management: Comprehensive tracking and management of your IT assets.</li>
    </ol>
    <h2 class="head head--blue" style="--rule:80%">Cloud Solutions</h2>
    <p class="body-copy" style="margin-top:12px;text-align:left">Embrace the power of the cloud with our scalable and secure cloud solutions. Our offerings include:</p>
    <ol class="num-list" style="margin-top:8px">
      <li><span>01.</span>Cloud Migration: Seamless transition of your applications and data to the cloud.</li>
      <li><span>02.</span>Cloud Hosting: Reliable and scalable hosting solutions to meet your growing needs.</li>
      <li><span>03.</span>Backup and Disaster Recovery: Robust backup and recovery solutions to ensure business continuity.</li>
      <li><span>04.</span>Software as a Service (SaaS): Access to the latest software applications without the hassle of maintenance.</li>
    </ol>
  </div>

  <div class="abs" style="left:507px;top:24px;width:204px;color:var(--white)">
    <h2 class="head" style="font-size:16px;--rule:0">Cybersecurity</h2>
    <p class="body-copy" style="margin-top:12px">Protect your business from evolving threats with our comprehensive cybersecurity services. We offer:</p>
    <ul class="dot-list" style="margin-top:10px">
      <li>Threat Detection and Response: Advanced threat monitoring and response to safeguard your data.</li>
      <li>Security Audits and Assessments: Thorough evaluations to identify and mitigate vulnerabilities.</li>
      <li>Endpoint Protection: Robust security solutions for all your devices.</li>
      <li>Compliance and Regulatory Services: Ensure adherence to industry standards and regulations.</li>
    </ul>
    <h2 class="head" style="font-size:16px;--rule:0;margin-top:14px">IT Consulting</h2>
    <p class="body-copy" style="margin-top:12px">Leverage our expertise to drive your IT strategy and achieve your business goals. Our consulting services include:</p>
  </div>
  <svg class="art" style="left:490px" width="249" height="575" viewBox="0 0 249 575">
    <defs>
      <linearGradient id="dataTone" x1="0" y1="0" x2="1" y2="1">
        <stop offset="0" stop-color="#1a3550"/>
        <stop offset="0.6" stop-color="#0f5c8c"/>
        <stop offset="1" stop-color="#0a2c48"/>
      </linearGradient>
    </defs>
    <path d="M0,362 Q140,372 205,575 L0,575 Z" fill="var(--blue)"/>
    <path d="M0,372 Q132,382 196,575 L0,575 Z" fill="url(#dataTone)" role="img" aria-label="Photo: rows of office workstations seen from above"/>
    <path d="M249,375 Q140,420 110,575 L249,575 Z" fill="#5a5a60"/>
    <path d="M249,384 Q146,428 118,575 L249,575 Z" fill="var(--blue)"/>
    <path d="M249,394 Q154,436 128,575 L249,575 Z" fill="url(#dataTone)" role="img" aria-label="Photo: glowing blue circuit and binary data pattern"/>
  </svg>
</section>

</body>
</html>
```